Walk Beside The River

Business Card design

Target Market(s)

People who require support in the commnity

Industry/Entity Type

Mental Health Support

Contact Information for Business Card

Mental Health Support Rosalind Tavener walkbesidetheriver@mailcove.com.au 0481 637 092 PO Box 926 Pelican Reach QLD 4571

Colors
6B429C
8869AF
B7A5CE
E3DAEB
F3F0F8

Requirements
Must have
• Logo & details listed above
Should not have
• No red or orange

```html
<!DOCTYPE html>
<html lang="en">
<head>
<meta charset="utf-8">
<title>Walk Beside The River – Business Card</title>
<link rel="stylesheet" href="https://fonts.googleapis.com/css2?family=Open+Sans:wght@400;600;700;800&display=swap">
<style>
  :root {
    --stage: #232323;
    --card-dark: #222226;
    --purple: #6B429C;
    --purple-mid: #8869AF;
    --purple-soft: #B7A5CE;
    --lavender: #E3DAEB;
    --cream: #F3F0F8;
    --yellow: #EFE82C;
    --ink: #111111;
  }
  * { box-sizing: border-box; margin: 0; padding: 0; }
  html, body { width: 1200px; height: 780px; overflow: hidden; }
  body {
    background: var(--stage);
    font-family: "Open Sans", Arial, sans-serif;
    display: flex;
    align-items: center;
    justify-content: center;
    gap: 40px;
  }
  .card {
    position: relative;
    width: 560px;
    height: 320px;
    border-radius: 18px;
    border: 3px solid var(--yellow);
    overflow: hidden;
  }

  /* Back side */
  .card--back { background: var(--purple); }
  .back-pattern {
    position: absolute; inset: 0;
    background: linear-gradient(200deg, var(--purple-mid) 0%, var(--purple) 45%, #5a3787 100%);
  }
  .back-mark {
    position: absolute;
    right: 40px; top: 118px;
    display: flex; align-items: center; gap: 8px;
    color: var(--cream);
    font-size: 11px; font-weight: 700;
    letter-spacing: 0.12em; text-transform: uppercase;
  }
  .back-mark__dot {
    width: 10px; height: 10px; border-radius: 50%;
    background: var(--yellow);
  }

  /* Front side */
  .card--front { background: var(--card-dark); }
  .brand-badge {
    position: absolute;
    right: 38px; top: 24px;
    width: 180px; height: 180px;
    border-radius: 50%;
    background: var(--purple);
    display: flex; align-items: center; justify-content: center;
    text-align: center;
    padding: 28px;
    color: var(--cream);
    font-size: 17px; font-weight: 700;
    letter-spacing: 0.14em; line-height: 1.4;
    text-transform: uppercase;
  }
  .name-block {
    position: absolute;
    left: 0; top: 96px;
    padding-left: 34px;
  }
  .name-block__bar {
    position: absolute;
    left: 0; top: 6px;
    width: 22px; height: 66px;
    background: var(--yellow);
  }
  .person-name {
    font-size: 30px; font-weight: 800; line-height: 1.1;
    color: var(--yellow);
    white-space: nowrap;
  }
  .person-name__surname { color: var(--purple); }
  .person-role {
    font-size: 15px; font-weight: 600;
    color: var(--cream);
    margin-top: 2px;
  }
  .contact-list {
    position: absolute;
    left: 34px; top: 188px;
    list-style: none;
  }
  .contact-list li {
    display: flex; align-items: center; gap: 10px;
    color: var(--cream);
    font-size: 14px; line-height: 22px;
    white-space: nowrap;
  }
  .contact-list svg { width: 14px; height: 14px; flex: none; }
  .tagline-band {
    position: absolute;
    left: 0; right: 0; top: 262px;
    height: 30px;
    background: var(--yellow);
    display: flex; align-items: center; justify-content: flex-end;
    padding-right: 42px;
    color: var(--ink);
    font-size: 15px; font-weight: 600;
    white-space: nowrap;
  }
</style>
</head>
<body>

  <section class="card card--back" aria-label="Business card, back">
    <div class="back-pattern" role="img" aria-label="Purple field scattered with a grid of soft star shapes fading to light sparkles at the top right"></div>
    <div class="back-mark">
      <span class="back-mark__dot"></span>
      <span>Walk Beside The River</span>
    </div>
  </section>

  <section class="card card--front" aria-label="Business card, front">
    <div class="brand-badge">Walk Beside The River</div>

    <div class="name-block">
      <span class="name-block__bar"></span>
      <h1 class="person-name">Marta <span class="person-name__surname">Kovalenko</span></h1>
      <p class="person-role">CEO/Director</p>
    </div>

    <ul class="contact-list">
      <li>
        <svg viewBox="0 0 24 24" fill="var(--yellow)" aria-hidden="true"><path d="M6.6 10.8a15.1 15.1 0 0 0 6.6 6.6l2.2-2.2a1 1 0 0 1 1-.25 11.4 11.4 0 0 0 3.6.57 1 1 0 0 1 1 1V20a1 1 0 0 1-1 1A17 17 0 0 1 3 4a1 1 0 0 1 1-1h3.5a1 1 0 0 1 1 1c0 1.25.2 2.45.57 3.57a1 1 0 0 1-.25 1z"/></svg>
        <span>0481 637 092</span>
      </li>
      <li>
        <svg viewBox="0 0 24 24" fill="none" stroke="var(--yellow)" stroke-width="2" aria-hidden="true"><rect x="3" y="5" width="18" height="14" rx="2"/><path d="M3 7l9 6 9-6"/></svg>
        <span>walkbesidetheriver@mailcove.com.au</span>
      </li>
      <li>
        <svg viewBox="0 0 24 24" fill="none" stroke="var(--yellow)" stroke-width="2" aria-hidden="true"><path d="M12 22s7-6.5 7-12a7 7 0 0 0-14 0c0 5.5 7 12 7 12z"/><circle cx="12" cy="10" r="2.5"/></svg>
        <span>PO Box 926 Pelican Reach QLD 4571</span>
      </li>
    </ul>

    <div class="tagline-band">Mental Health Support Rosalind Tavener</div>
  </section>

</body>
</html>
```